Velmora Wheel Outings company needs new Web Design

We need a new design for our main website. You can find the wireframe(file # 12) for the homepage in uploaded files. Firstly we want a design for the homepage (Please take a look at last uploaded file #12 for more information). If we like it we would also need designs for other subpages (section detail page, tour detail page, reservation form, FAQ, photogallery, search results, blog and basic content page). All wireframes are ready, we need design, graphics, colors ideas.
Our current page is: http://www.tovarkolo.cz. The logo and information content should remain the same.
Updates

Notes for Tovarkolo.cz  -new web site 2014

 

There is new file uploaded with notes. Its a draft But Its just square boxes, and boring..we need some creativity, some curves, shapes…. Motions.

Bikes elements could be used, wheel shapes.. 

Web site should show that bikes is the best way of getting around, itsecological, green, fun and healthy. 

The new file is uploaded for more explanation, ideas, layouts and notes.

Reason: We still dont see the good interesting design ideas.

Reason: New updates in uploaded file #12.

We are looking for an exciting  original design; bike parts as chain, wheels, frames, nature elements.. can be used as borders for blocks. Decent background with bike wheel traces, or bike elements, some graphic and fun stuff to show that its not just a bike shop But bike tour company providing fun, active and informational experience!

Also check the updated brief and file#12.

Reason: Not available for close communication from Dec 7 till Dec 13

Reason: Winter holidays

Target Market(s)

Our customers are mostly tourists visiting Prague interested in active, informational and fun way to see the city; including big student and company groups, families, independent travelers; age from 16 to 75. Please take a look at last uploaded file #12 for more information.

Industry/Entity Type

It Company

Requirements
Must have
• Exciting original design, bike parts as chain, wheel.. can be used as borders for blocks. Decent background with bike wheel traces, or bike elements, some graphic and fun stuff to show that its not just a bike shop But bike tour company providing fun, active and informational experience!
Nice to have
• -web visitors should easily see the different kind of services/tours we offer
-impression should be sporty/active but not too much as our services are suitable for people who are not active on daily bases as well using the bike as the way of transportation not as the sport/adrenalin tool.

```html
<!DOCTYPE html>
<html lang="en">
<head>
<meta charset="utf-8">
<title>Velmora Wheel Outings</title>
<link href="https://fonts.googleapis.com/css2?family=Arimo:wght@400;700&family=Lilita+One&display=swap" rel="stylesheet">
<style>
:root{
  --orange:#e8822a;--orange-2:#c96f1c;--orange-3:#a65b15;--orange-4:#7f4510;
  --green:#8aae1f;--green-2:#6f8d19;--green-3:#587214;--green-4:#43580e;
  --blue:#55b2de;--blue-2:#4096bd;--blue-3:#347e9f;--blue-4:#296480;
  --nav:#3b3b3b;--ink:#222;--grey:#d9d9d9;--line:#ddd;--white:#fff;
}
*{box-sizing:border-box;margin:0;padding:0}
html,body{width:812px;height:1200px;overflow:hidden;background:var(--white);font-family:"Arimo",Arial,sans-serif;color:var(--ink)}
.page{position:relative;width:650px;margin-left:81px}
.header{height:104px;position:relative}
.brand{position:absolute;left:0;top:22px;display:flex;align-items:center;gap:10px}
.brand-mark{width:56px;height:56px;border-radius:50%;background:var(--orange)}
.brand-name{font-family:"Arimo",sans-serif;font-weight:700;font-size:20px;color:var(--orange);line-height:1.1;width:150px}
.flags{position:absolute;right:0;top:4px;display:flex;gap:8px}
.flag{width:20px;height:14px;background:#8aa0c8}
.flag:nth-child(2){background:#9fb4d8}.flag:nth-child(3){background:#4aa3c9}.flag:nth-child(4){background:#b64a2e}
.social{position:absolute;left:418px;top:54px;display:flex;gap:8px}
.social span{width:18px;height:18px;border-radius:50%;border:2px solid #3b5998}
.social span+span{width:28px;border-color:#222}
.search{position:absolute;right:0;top:54px;width:146px;height:20px;background:#111;border-radius:3px;color:#999;font-size:11px;padding:3px 8px}
.search svg{position:absolute;right:5px;top:4px}
.nav{display:flex;height:28px;background:var(--nav);border-radius:3px;overflow:hidden}
.nav a{color:#fff;text-decoration:none;font-size:12px;padding:0 11px;line-height:28px}
.nav a.active{background:var(--orange)}
.hero{display:flex;gap:4px;margin-top:4px;height:227px}
.hero-photo{width:372px;background:linear-gradient(135deg,#e9dcc0,#c7a47a 55%,#7d5b43);position:relative}
.dots{position:absolute;left:8px;bottom:8px;display:flex;gap:3px}
.dots i{width:6px;height:6px;border-radius:50%;background:#ddd}
.dots i:nth-child(2){background:#333}
.video{flex:1;background:#000;position:relative}
.video .play{position:absolute;left:50%;top:50%;transform:translate(-50%,-60%)}
.video .bar{position:absolute;left:0;right:0;bottom:0;height:14px;background:#1a1a1a;color:#aaa;font-size:7px;padding:3px 20px}
.cards{display:flex;gap:6px;margin-top:6px}
.card{width:213px;border-radius:4px 4px 0 0;overflow:hidden;color:#fff}
.card.green{background:var(--green)}.card.blue{background:var(--blue)}.card.orange{background:var(--orange)}
.card h2{font-family:"Lilita One",sans-serif;font-weight:400;font-size:20px;text-align:center;height:40px;line-height:42px;letter-spacing:.5px}
.card-photo{margin:0 8px;height:162px;border-radius:3px;position:relative;overflow:hidden}
.green .card-photo{background:linear-gradient(160deg,#b8a58e,#6b5a4c)}
.blue .card-photo{background:linear-gradient(160deg,#c9d8e4,#8a7c6c)}
.orange .card-photo{background:linear-gradient(160deg,#d9ccb8,#6d6a5e)}
.card-photo span{position:absolute;left:0;right:0;bottom:0;height:30px;background:rgba(0,0,0,.85);font-family:"Lilita One",sans-serif;font-size:17px;text-align:center;line-height:31px;border-radius:6px 6px 0 0}
.card p{font-size:12px;line-height:16px;text-align:center;padding:10px 18px 12px;height:103px}
.card a{display:block;font-family:"Lilita One",sans-serif;font-size:15px;text-align:center;color:#fff;text-decoration:none;height:37px;line-height:38px}
.green .l1{background:var(--green-2)}.green .l2{background:var(--green-3)}.green .l3{background:var(--green-4)}
.blue .l1{background:var(--blue-2)}.blue .l2{background:var(--blue-3)}.blue .l3{background:var(--blue-4)}
.orange .l1{background:var(--orange-2)}.orange .l2{background:var(--orange-3)}.orange .l3{background:var(--orange-4)}
.location{display:flex;gap:6px;margin-top:6px;height:141px}
.map{width:432px;background:linear-gradient(120deg,#ecebe6,#dcdad3);border-radius:3px}
.address{flex:1;background:var(--grey);border-radius:3px;padding:10px;font-size:12px;line-height:19px}
.address .title{font-size:12.5px}
.bottom{display:flex;gap:10px;margin-top:9px;height:200px}
.review{width:212px;border:1px solid var(--green);border-radius:3px;position:relative;padding:10px 14px}
.review-brand{display:flex;align-items:center;gap:6px;font-size:13px;border-bottom:1px solid #ccc;padding-bottom:8px}
.review-brand i{width:14px;height:14px;border-radius:50%;background:#222}
.review h3{font-size:11px;margin-top:8px}
.rate{display:flex;gap:2px;margin-top:4px;align-items:center;font-size:11px;color:#2b7a1a}
.rate i{width:10px;height:10px;border-radius:50%;border:1px solid #777}
.rate em{font-style:normal;margin-left:4px}
.review textarea{display:block;width:100%;height:66px;margin-top:4px;border:1px solid #8aae1f;font:10px "Arimo",sans-serif;color:#999;padding:4px;resize:none}
.btn{display:inline-block;margin-top:10px;background:var(--orange);color:#fff;font-size:10px;font-weight:700;padding:2px 12px;border-radius:8px}
.powered{position:absolute;left:0;right:0;bottom:0;height:12px;background:var(--green);color:#fff;font-size:8px;font-style:italic;text-align:right;padding-right:6px;line-height:12px}
.promo{width:209px;border:1px solid var(--orange);border-radius:3px;overflow:hidden}
.promo.team{border-color:var(--blue)}
.promo h2{font-family:"Lilita One",sans-serif;font-weight:400;font-size:19px;color:#fff;text-align:center;height:34px;line-height:36px;background:var(--orange)}
.promo.team h2{background:var(--blue)}
.promo-photo{height:164px;background:linear-gradient(160deg,#d6d2c8,#9a8070 60%,#c73a3a)}
.team .promo-photo{background:linear-gradient(160deg,#bcd7ec,#6f9a4f 60%,#3f6ea8)}
.footer{margin-top:20px;border-top:1px solid var(--line);display:flex;font-size:12px;padding-top:12px}
.footer a{color:var(--ink);text-decoration:none;margin-right:22px}
.footer a.active{color:var(--orange)}
.footer .copy{margin-left:auto}
</style>
</head>
<body>
<div class="page">
  <header class="header">
    <div class="brand"><span class="brand-mark"></span><span class="brand-name">Velmora Wheel Outings</span></div>
    <div class="flags"><span class="flag"></span><span class="flag"></span><span class="flag"></span><span class="flag"></span></div>
    <div class="social"><span></span><span></span></div>
    <div class="search">Search
      <svg width="12" height="12" viewBox="0 0 12 12"><circle cx="5" cy="5" r="3.5" fill="none" stroke="#e8822a" stroke-width="2"/><line x1="7.5" y1="7.5" x2="11" y2="11" stroke="#e8822a" stroke-width="2"/></svg>
    </div>
  </header>
  <nav class="nav">
    <a class="active">Home</a><a>Bike Tours</a><a>Private Tours</a><a>About</a><a>Blog</a><a>FAQ</a><a>Contact</a><a>Reservation</a>
  </nav>
  <section class="hero">
    <div class="hero-photo" role="img" aria-label="Couple riding a bicycle together on a city street">
      <div class="dots"><i></i><i></i><i></i><i></i><i></i></div>
    </div>
    <div class="video" role="img" aria-label="Tour video player">
      <svg class="play" width="16" height="18" viewBox="0 0 16 18"><path d="M0 0L16 9L0 18Z" fill="#fff"/></svg>
      <div class="bar">0:06 / 3:14</div>
    </div>
  </section>
  <section class="cards">
    <article class="card green">
      <h2>CITY TOURS</h2>
      <div class="card-photo" role="img" aria-label="Rider with a basket bicycle in the old town"><span>BEST SELLER TOURS</span></div>
      <p>Lorem ipsum dolor sit amet, sectetur adipiscing elit. Sed id tempus enim. Etiam eros velit, rutrum in fringilla id, fermentum sit amet nulla. Nullam</p>
      <a class="l1">CLASSIC CITY BIKE TOUR</a><a class="l2">PANORAMIC BIKE TOUR</a><a class="l3">BEER GARDEN TOUR</a>
    </article>
    <article class="card blue">
      <h2>COUNTRY TOURS</h2>
      <div class="card-photo" role="img" aria-label="Cyclist in a helmet riding through town"><span>RECOMMENDED TOUR</span></div>
      <p>Lorem ipsum dolor sit amet, sectetur adipiscing elit. Sed id tempus enim. Etiam eros velit, rutrum in fringilla id, fermentum sit amet nulla. Nullam</p>
      <a class="l1">CLASSIC CITY BIKE TOUR</a><a class="l2">PANORAMIC BIKE TOUR</a><a class="l3">BEER GARDEN TOUR</a>
    </article>
    <article class="card orange">
      <h2>BIKE RENTAL</h2>
      <div class="card-photo" role="img" aria-label="Rider walking a rental bike above the rooftops"><span>YOU MIGHT ALSO LIKE</span></div>
      <p>Lorem ipsum dolor sit amet, sectetur adipiscing elit. Sed id tempus enim. Etiam eros velit, rutrum in fringilla id, fermentum sit amet nulla. Nullam</p>
      <a class="l1">CLASSIC CITY BIKE TOUR</a><a class="l2">PANORAMIC BIKE TOUR</a><a class="l3">BEER GARDEN TOUR</a>
    </article>
  </section>
  <section class="location">
    <div class="map" role="img" aria-label="Street map showing the meeting point"></div>
    <div class="address">
      <div class="title">OUR ADDRESS &amp; MEETING POINT:</div>
      <div>Kovářská 18, Prague 1</div>
      <div><b>OPEN DAILY:</b> 09:00 - 21:00</div>
      <div><b>EMAIL:</b> info@tovarkolo.cz</div>
      <div><b>TEL:</b> +420 700 555 014</div>
    </div>
  </section>
  <section class="bottom">
    <div class="review">
      <div class="review-brand"><i></i>ReviewNest</div>
      <h3>Review The Linden Yard House</h3>
      <div class="rate"><i></i><i></i><i></i><i></i><i></i><em>(Click to rate)</em></div>
      <textarea>Title your review - Describe your stay in one sentence or less.</textarea>
      <span class="btn">Continue</span>
      <div class="powered">powered by ReviewNest</div>
    </div>
    <div class="promo">
      <h2>SPECIAL OFFERS</h2>
      <div class="promo-photo" role="img" aria-label="Group of friends cycling through the city"></div>
    </div>
    <div class="promo team">
      <h2>TEAM BIKE TOURS</h2>
      <div class="promo-photo" role="img" aria-label="Family riding bicycles in a park"></div>
    </div>
  </section>
  <footer class="footer">
    <a class="active">Home</a><a>Private</a><a>Tours</a><a>Photos</a><a>FAQ</a><a>Reservation</a><a>Links</a><a>Contact</a>
    <span class="copy">Copyright 2013. Tovarkolo</span>
  </footer>
</div>
</body>
</html>
```